Animal Eye Clinic needs a Business card

We are a new veterinary ophthalmology practice (Ridgeline Pet Vision Care) and we need a business card designed. We only see animal eyes - we are not a regular veterinary clinic. We already have a logo. We are looking for a professional, good looking business card to hand out to our clients. We are looking for something simple but professional and contemporary. Our logo is likely the only picture/graphic that needs to be on the card.
Updates

Contact Information for Business Card

Delia Vossman, BSc, DVM, MSc, DipACVO
Veterinary Ophthalmologist

Phone: 250.418.3927
Email: ridgelinepetvisioncare@mailbox-example.net
Website: ridgelinepetvisioncare-example.net
Address: 1874 Thornbury Rd
Kelowna, BC, V1X 4M9

Colors

Designer to choose colors to be used in the design.

Requirements
Must have
• Our logo (attached)

```html
<!DOCTYPE html>
<html lang="en">
<head>
<meta charset="utf-8">
<title>Ridgeline Pet Vision Care – Business Card</title>
<link rel="stylesheet" href="https://fonts.googleapis.com/css2?family=Lato:wght@300;400;700&display=swap">
<style>
  :root {
    --teal: #1a9aa8;
    --teal-soft: #4fb6c1;
    --white: #ffffff;
    --ink: #1d1d1d;
    --grey: #9a9a9a;
    --grey-band: #8c8c8c;
    --rule: #b5b5b5;
    --backdrop: #1f1f1f;
  }
  * { margin: 0; padding: 0; box-sizing: border-box; }
  html, body {
    width: 1200px; height: 900px; overflow: hidden;
    background: var(--backdrop);
    font-family: "Lato", Arial, sans-serif;
  }
  .canvas { position: relative; width: 1200px; height: 900px; }

  .card {
    position: absolute;
    width: 600px; height: 343px;
    border-radius: 18px;
    overflow: hidden;
  }

  /* Back side */
  .card--back { left: 60px; top: 80px; background: var(--teal); }
  .card--back .pattern {
    position: absolute; inset: 0;
    background: linear-gradient(135deg, var(--teal) 0%, #1fa3b1 50%, var(--teal) 100%);
  }
  .card--back .brand {
    position: absolute; left: 0; right: 0; top: 120px;
    display: flex; align-items: center; justify-content: center; gap: 14px;
  }
  .card--back .brand-dot {
    width: 40px; height: 40px; border-radius: 50%; background: var(--white);
  }
  .card--back .brand-name {
    color: var(--white); font-weight: 700; font-size: 26px; letter-spacing: 1px;
    text-transform: uppercase;
  }
  .card--back .website {
    position: absolute; left: 0; right: 0; bottom: 62px;
    text-align: center; color: var(--white);
    font-size: 14px; font-weight: 700; letter-spacing: 2px;
  }

  /* Front side */
  .card--front { left: 540px; top: 477px; background: var(--white); }
  .card--front .brand {
    position: absolute; left: 70px; top: 72px;
    display: flex; align-items: center; gap: 12px;
  }
  .card--front .brand-dot {
    width: 42px; height: 42px; border-radius: 50%; background: var(--teal);
  }
  .card--front .brand-name {
    color: var(--teal); font-weight: 700; font-size: 24px; letter-spacing: 0.5px;
    text-transform: uppercase;
  }
  .person {
    position: absolute; right: 345px; top: 182px; text-align: right; white-space: nowrap;
  }
  .person-name {
    color: var(--teal); font-weight: 400; font-size: 18px; letter-spacing: 0.5px;
    text-transform: uppercase;
  }
  .person-credentials { color: var(--grey); font-weight: 300; font-size: 14px; margin-top: 3px; }
  .person-title { color: var(--ink); font-weight: 700; font-size: 14px; margin-top: 5px; }
  .divider {
    position: absolute; left: 268px; top: 178px; width: 1px; height: 84px; background: var(--rule);
  }
  .contacts {
    position: absolute; left: 284px; top: 182px; list-style: none;
  }
  .contacts li {
    display: flex; align-items: center; gap: 8px; white-space: nowrap;
    font-size: 12px; color: var(--ink); height: 24px;
  }
  .contacts .address { color: var(--teal); font-size: 12.5px; padding-left: 22px; }
  .contacts svg { width: 14px; height: 14px; flex: none; }
  .front-band { position: absolute; left: 0; bottom: 0; width: 600px; height: 60px; }
</style>
</head>
<body>
<main class="canvas">

  <section class="card card--back" aria-label="Business card back">
    <div class="pattern" role="img" aria-label="Light paw print pattern on teal"></div>
    <div class="brand">
      <span class="brand-dot"></span>
      <span class="brand-name">Ridgeline Pet Vision Care</span>
    </div>
    <p class="website">www.ridgelinepetvisioncare-example.net</p>
  </section>

  <section class="card card--front" aria-label="Business card front">
    <div class="brand">
      <span class="brand-dot"></span>
      <span class="brand-name">Ridgeline Pet Vision Care</span>
    </div>

    <div class="person">
      <p class="person-name">Delia Vossman</p>
      <p class="person-credentials">BSc, DVM, MSc, DipACVO</p>
      <p class="person-title">Veterinary Ophthalmologist</p>
    </div>

    <span class="divider"></span>

    <ul class="contacts">
      <li>
        <svg viewBox="0 0 16 16" aria-hidden="true"><path fill="#1a9aa8" d="M3 2h3l1.5 3.5-2 1.3a8 8 0 0 0 3.7 3.7l1.3-2L14 10v3a1 1 0 0 1-1 1A11 11 0 0 1 2 3a1 1 0 0 1 1-1z"/></svg>
        250.418.3927
      </li>
      <li>
        <svg viewBox="0 0 16 16" aria-hidden="true"><rect x="1.5" y="3.5" width="13" height="9" fill="#1a9aa8"/><path d="M1.5 3.5 8 9l6.5-5.5" fill="none" stroke="#fff" stroke-width="1.2"/></svg>
        ridgelinepetvisioncare@mailbox-example.net
      </li>
      <li class="address">1874 Thornbury Rd, Kelowna, BC, V1X 4M9</li>
    </ul>

    <svg class="front-band" viewBox="0 0 600 60" preserveAspectRatio="none" aria-hidden="true">
      <path d="M0 50 L410 30 L410 60 L0 60 Z" fill="var(--teal)"/>
      <path d="M410 60 L410 30 Q425 8 460 7 L600 0 L600 60 Z" fill="var(--grey-band)"/>
    </svg>
  </section>

</main>
</body>
</html>
```